TALVORE GROUP OF CLINICS

We need a medical & lab report file. The design should be healthcare related. Our current file design has been used for almost 10 years. We need something more fresh & up-to-date. We have attached the current file design.

Need extra days to review

```html
<!DOCTYPE html>
<html lang="en">
<head>
<meta charset="utf-8">
<title>Talvore Group of Clinics – Medical Report Folder</title>
<link href="https://fonts.googleapis.com/css2?family=Montserrat:wght@500;600;700;800;900&display=swap" rel="stylesheet">
<style>
:root{
  --navy:#1b2f6b;
  --navy-deep:#14245a;
  --blue:#2f7fd0;
  --sky:#5aa8e8;
  --ice:#dcecfa;
  --paper:#ffffff;
  --stage:#eef0f3;
  --ink:#2b3550;
}
*{margin:0;padding:0;box-sizing:border-box}
html,body{width:800px;height:1200px;overflow:hidden}
body{background:var(--stage);font-family:"Montserrat",Arial,sans-serif;color:var(--ink);position:relative}
.spread{position:absolute;left:10px;top:330px;width:780px;height:540px;display:flex;box-shadow:0 4px 18px rgba(20,36,90,.15)}
.panel{position:relative;width:390px;height:540px;overflow:hidden;background:var(--paper)}
.panel-back{border-right:1px solid #d7e2ee}
.hex-field{position:absolute;left:0;right:0;bottom:0;height:260px;background:linear-gradient(180deg,rgba(255,255,255,0) 0%,var(--ice) 60%,#b9d8f4 100%)}
.hex-field.top{top:0;bottom:auto;height:300px;background:linear-gradient(200deg,#b9d8f4 0%,var(--ice) 35%,rgba(255,255,255,0) 75%)}
.group-title{position:absolute;left:22px;top:26px;font-size:19px;font-weight:800;color:var(--navy);letter-spacing:.2px}
.group-title span{color:var(--blue)}
.title-rule{position:absolute;left:22px;top:52px;width:346px;height:2px;background:var(--navy)}
.clinic-grid{position:absolute;left:22px;top:70px;width:346px;display:grid;grid-template-columns:1fr 1fr;gap:14px 12px}
.clinic{position:relative;border:1.5px solid var(--navy);border-radius:6px;background:rgba(255,255,255,.92);padding:26px 8px 8px;height:98px}
.clinic-name{position:absolute;left:-1px;top:-1px;right:-1px;background:var(--navy);color:#fff;font-size:8.5px;font-weight:700;line-height:1.2;padding:3px 8px;border-radius:5px 5px 0 0}
.clinic-name small{display:block;font-size:7.5px;font-weight:600;color:#cfe3f8}
.line{display:flex;align-items:center;gap:5px;font-size:7.5px;font-weight:500;line-height:1.35;margin-top:2px}
.line svg{width:9px;height:9px;flex:none;fill:var(--blue)}
.clinic.solo{grid-column:1}
.brand{position:absolute;left:0;right:0;top:26px;display:flex;flex-direction:column;align-items:center;gap:6px}
.brand-dot{width:34px;height:34px;border-radius:50%;background:var(--blue)}
.brand-name{font-size:9px;font-weight:700;color:var(--navy);letter-spacing:1px}
.cover-title{position:absolute;left:0;right:0;top:106px;text-align:center;font-size:62px;font-weight:900;color:var(--navy);letter-spacing:1px}
.globe{position:absolute;left:135px;top:186px;width:120px;height:120px;border-radius:50%;background:radial-gradient(circle at 38% 35%,#8fd0f7 0%,var(--blue) 55%,var(--navy) 100%)}
.cover-sub{position:absolute;left:0;right:0;top:312px;text-align:center;font-size:38px;font-weight:800;color:var(--navy);letter-spacing:3px}
.tagline{position:absolute;left:0;right:0;top:372px;text-align:center;font-size:20px;font-weight:800;color:var(--navy)}
.confidential{position:absolute;left:60px;right:60px;top:406px;height:26px;background:var(--navy);color:#fff;font-size:12px;font-weight:700;letter-spacing:1.5px;display:flex;align-items:center;justify-content:center}
.web{position:absolute;left:0;right:0;top:444px;text-align:center;font-size:15px;font-weight:800;color:var(--navy-deep)}
</style>
</head>
<body>
<svg width="0" height="0" style="position:absolute">
  <defs>
    <symbol id="i-pin" viewBox="0 0 10 10"><path d="M5 0a3.5 3.5 0 0 0-3.5 3.5C1.5 6 5 10 5 10s3.5-4 3.5-6.5A3.5 3.5 0 0 0 5 0zm0 5a1.4 1.4 0 1 1 0-2.8A1.4 1.4 0 0 1 5 5z"/></symbol>
    <symbol id="i-phone" viewBox="0 0 10 10"><path d="M2 .5l1.6 2.2-1 1.2a6 6 0 0 0 3.5 3.5l1.2-1L9.5 8 8.3 9.5C4 9.5.5 6 .5 1.7z"/></symbol>
    <symbol id="i-fax" viewBox="0 0 10 10"><path d="M2.5 0h5v3h-5zM1 3.5h8v4H7.5V10h-5V7.5H1zm2.5 3v2.5h3V6.5z"/></symbol>
    <symbol id="i-mail" viewBox="0 0 10 10"><path d="M0 2h10v6H0zm1 .8v.4l4 2.5 4-2.5v-.4z"/></symbol>
  </defs>
</svg>

<main class="spread">
  <section class="panel panel-back">
    <div class="hex-field" role="img" aria-label="Soft blue hexagon pattern background"></div>
    <h2 class="group-title">TALVORE GROUP <span>OF CLINICS</span></h2>
    <div class="title-rule"></div>
    <div class="clinic-grid">
      <article class="clinic">
        <h3 class="clinic-name">PUSAT PERUBATAN<small>TALVORE</small></h3>
        <p class="line"><svg><use href="#i-pin"/></svg>No. 12, Jalan Seroja, Seranti</p>
        <p class="line"><svg><use href="#i-phone"/></svg>082-5550101</p>
        <p class="line"><svg><use href="#i-fax"/></svg>082-5550102</p>
        <p class="line"><svg><use href="#i-mail"/></svg>pusat@talvore.my</p>
      </article>
      <article class="clinic">
        <h3 class="clinic-name">KLINIK TALVORE<small>(BUKIT SERANTI)</small></h3>
        <p class="line"><svg><use href="#i-pin"/></svg>Lot 8, Lorong Kenari, Seranti</p>
        <p class="line"><svg><use href="#i-phone"/></svg>082-5550201</p>
        <p class="line"><svg><use href="#i-fax"/></svg>082-5550202</p>
        <p class="line"><svg><use href="#i-mail"/></svg>seranti@talvore.my</p>
      </article>
      <article class="clinic">
        <h3 class="clinic-name">KLINIK TALVORE<small>(BATU KERIS)</small></h3>
        <p class="line"><svg><use href="#i-pin"/></svg>No. 3, Jalan Cempaka, Keris</p>
        <p class="line"><svg><use href="#i-phone"/></svg>082-5550301</p>
        <p class="line"><svg><use href="#i-fax"/></svg>082-5550302</p>
        <p class="line"><svg><use href="#i-mail"/></svg>keris@talvore.my</p>
      </article>
      <article class="clinic">
        <h3 class="clinic-name">KLINIK TALVORE<small>(SELUNDAN)</small></h3>
        <p class="line"><svg><use href="#i-pin"/></svg>Lot 21, Taman Melati, Selundan</p>
        <p class="line"><svg><use href="#i-phone"/></svg>082-5550401</p>
        <p class="line"><svg><use href="#i-fax"/></svg>082-5550402</p>
        <p class="line"><svg><use href="#i-mail"/></svg>selundan@talvore.my</p>
      </article>
      <article class="clinic">
        <h3 class="clinic-name">TALVORE MEDICAL CLINIC<small>(PANTAI INDAH)</small></h3>
        <p class="line"><svg><use href="#i-pin"/></svg>No. 5, Jalan Pantai, Indah</p>
        <p class="line"><svg><use href="#i-phone"/></svg>085-5550501</p>
        <p class="line"><svg><use href="#i-fax"/></svg>085-5550502</p>
        <p class="line"><svg><use href="#i-mail"/></svg>pantai@talvore.my</p>
      </article>
      <article class="clinic">
        <h3 class="clinic-name">TALVORE MEDICAL CLINIC<small>(TANJUNG RIMBA)</small></h3>
        <p class="line"><svg><use href="#i-pin"/></svg>Lot 40, Jalan Dahlia, Rimba</p>
        <p class="line"><svg><use href="#i-phone"/></svg>086-5550601</p>
        <p class="line"><svg><use href="#i-fax"/></svg>086-5550602</p>
        <p class="line"><svg><use href="#i-mail"/></svg>rimba@talvore.my</p>
      </article>
      <article class="clinic solo">
        <h3 class="clinic-name">TALVORE MEDICAL CLINIC<small>(BANDAR PUJAN)</small></h3>
        <p class="line"><svg><use href="#i-pin"/></svg>No. 9, Lorong Orkid, Pujan</p>
        <p class="line"><svg><use href="#i-phone"/></svg>084-5550701</p>
        <p class="line"><svg><use href="#i-fax"/></svg>084-5550702</p>
        <p class="line"><svg><use href="#i-mail"/></svg>pujan@talvore.my</p>
      </article>
    </div>
  </section>

  <section class="panel panel-cover">
    <div class="hex-field top" role="img" aria-label="Soft blue hexagon pattern background"></div>
    <div class="brand">
      <span class="brand-dot"></span>
      <span class="brand-name">TALVORE GROUP</span>
    </div>
    <h1 class="cover-title">MEDICAL</h1>
    <div class="globe" role="img" aria-label="Illustration of a blue globe with a stethoscope"></div>
    <p class="cover-sub">REPORT</p>
    <p class="tagline">Your healthcare partner</p>
    <p class="confidential">PRIVATE &amp; CONFIDENTIAL</p>
    <p class="web">www.talvore.my</p>
  </section>
</main>
</body>
</html>
```